A website for a Maltese Law Firm

Our law firm needs a website to further its business. The site should have a simple yet effective design. We would need the following sections: About us, Practice Areas, About Malta, Contact. These should be further split as follows:

About us: Our firm, Our values, What others say, Offices

Practice Areas: Crimimal, Citizenship & Residence, Sovereign Patron Pathway, Criminal Defence, Civil Litigation, Arbitration and ADR, Commercial and Corporate, Media Law.

About Malta: just one section.

Contact: Just one section

We would also need a news feed at the front of the site to include latest news regarding our cases.

At the bottom we need a section for our Terms and a Privacy Statement.

Our logo is being attached.

Target Market(s)

All clients looking for legal assistance in Malta

Industry/Entity Type

Legal

Coding

Coded - Design and coding required

Number of Pages Required

1 page

Requirements
Must have
• It must be simple yet striking.

```html
<!DOCTYPE html>
<html lang="en">
<head>
<meta charset="utf-8">
<title>Delmara &amp; Castell Advocates</title>
<link href="https://fonts.googleapis.com/css2?family=Gentium+Book+Plus:ital,wght@0,400;0,700;1,400;1,700&display=swap" rel="stylesheet">
<style>
:root{
  --ink:#1b1b1b;
  --black:#050505;
  --header:#1c1c1c;
  --light:#efefef;
  --white:#ffffff;
  --text:#333333;
  --muted:#7a7a7a;
  --line:#cfcfcf;
  --footer-base:#e4e4e4;
  --hero-photo-a:#2a2a2a;
  --hero-photo-b:#8d8d8d;
}
*{margin:0;padding:0;box-sizing:border-box}
html,body{width:1200px;height:2635px;overflow:hidden}
body{position:relative;background:var(--white);font-family:"Gentium Book Plus",Georgia,serif;color:var(--text)}
.abs{position:absolute}

/* header */
.site-header{left:0;top:0;width:1200px;height:109px;background:var(--header);border-bottom:2px solid #4a4a4a}
.wordmark{font-size:21px;line-height:1;font-weight:400;white-space:nowrap}
.site-header .wordmark{left:144px;top:43px;color:var(--white)}
.main-nav a{position:absolute;top:42px;color:#e6e6e6;font-size:17px;text-decoration:none;white-space:nowrap}
.main-nav a.active{border-bottom:1px solid #bbb;padding-bottom:10px}

/* hero */
.hero{left:0;top:111px;width:1200px;height:483px;background:#101010}
.hero-photo{left:548px;top:0;width:652px;height:483px;background:radial-gradient(ellipse at 50% 40%,var(--hero-photo-b),var(--hero-photo-a) 75%)}
.hero-title{left:144px;top:199px;color:var(--white);font-size:32px;line-height:38px;font-weight:400}
.btn-ghost{border:1px solid #8a8a8a;color:#cfcfcf;font-size:12px;padding:3px 14px;text-decoration:none}
.hero .btn-ghost{left:144px;top:297px}
.hero-dots{left:144px;top:433px;display:flex;gap:12px}
.hero-dots span{width:9px;height:9px;border-radius:50%;background:#666}
.hero-dots span.on{background:#eee}

/* practice */
.practice{left:0;top:594px;width:1200px;height:654px;background:var(--light)}
.section-title{width:1200px;text-align:center;font-size:34px;color:#222;font-weight:400}
.practice .section-title{top:48px}
.area-card{top:139px;width:211px}
.area-photo{width:211px;height:189px;background:linear-gradient(160deg,#4a4a4a,#1e1e1e);position:relative}
.area-photo h3{position:absolute;left:22px;top:112px;color:#f2f2f2;font-weight:400;font-size:18px;line-height:24px}
.area-card p{margin-top:27px;font-size:10.5px;line-height:19.5px;color:#888}
.btn-read{display:inline-block;margin-top:23px;border:1px solid #9a9a9a;color:#555;font-size:12px;padding:2px 6px;text-decoration:none;background:transparent}
.scroll-track{left:144px;top:570px;width:912px;height:15px;border-radius:8px;background:linear-gradient(#f9f9f9,#d9d9d9);border:1px solid #c8c8c8}
.scroll-thumb{left:2px;top:2px;width:55px;height:9px;border-radius:5px;background:#8a8a8a}

/* news */
.news-band{left:0;top:1248px;width:1200px;height:123px;background:var(--black)}
.news-band .section-title{top:44px;color:var(--white)}
.news-pointer{left:586px;top:1370px}
.news{left:0;top:1371px;width:1200px;height:483px;background:var(--white)}
.news-card{top:54px;width:287px;text-align:center}
.news-photo{height:178px;background:linear-gradient(150deg,#b5b5b5,#3a3a3a);position:relative;box-shadow:0 8px 10px -8px rgba(0,0,0,.5)}
.news-date{position:absolute;left:88px;top:42px;width:111px;height:94px;background:rgba(0,0,0,.55);color:#eee;font-size:18px;line-height:21px;padding-top:12px}
.news-card h4{margin-top:22px;font-weight:400;font-size:13.5px;line-height:21px;color:#222}
.news-card p{margin-top:14px;font-size:10.5px;line-height:17px;color:#888}
.news-card .btn-read{margin-top:16px}
.nav-arrow{top:236px}

/* testimonials */
.testimonials{left:0;top:1854px;width:1200px;height:379px;background:radial-gradient(ellipse at 60% 40%,#3a3a3a,#141414 80%)}
.testimonials .section-title{top:53px;color:var(--white)}
.partner{left:199px;top:192px;width:200px;display:flex;align-items:center;gap:10px;color:#bdbdbd;font-size:15px}
.partner i{width:26px;height:26px;background:#8e8e8e;display:block}
.quote-divider{left:420px;top:168px;width:1px;height:106px;background:#777}
.quote{left:455px;top:182px;width:630px;color:#ddd;font-size:13px;line-height:24px}
.quote-nav{left:560px;top:310px;display:flex;align-items:center;gap:14px}
.quote-nav .sep{width:1px;height:36px;background:#888}

/* footer */
.site-footer{left:0;top:2233px;width:1200px;height:283px;background:var(--white)}
.site-footer .wordmark{left:0;top:48px;width:1200px;text-align:center;color:#222}
.footer-rule{left:142px;top:107px;width:914px;height:1px;background:var(--line)}
.footer-col{top:130px;list-style:none;font-size:11.5px;line-height:24px;color:#222}
.footer-col li{white-space:nowrap}
.social li{display:flex;justify-content:space-between;width:80px;align-items:center}
.social b{width:8px;height:8px;border-radius:50%;background:#333;display:block}
.legal{left:0;top:2516px;width:1200px;height:119px;background:linear-gradient(#ededed,var(--footer-base))}
.legal-text{left:142px;top:24px;width:914px;text-align:center;font-size:11px;line-height:21px;color:#777}
.legal-text em{font-weight:700;color:#444}
.legal-rule{left:142px;top:70px;width:914px;height:1px;background:#c9c9c9}
.copyright{left:0;top:90px;width:1200px;text-align:center;font-size:11px;color:#444}
</style>
</head>
<body>

<header class="site-header abs">
  <div class="wordmark abs">Delmara &amp; Castell Advocates</div>
  <nav class="main-nav">
    <a class="active" style="left:506px">Home</a>
    <a style="left:590px">About Us</a>
    <a style="left:700px">Practice Areas</a>
    <a style="left:850px">About Malta</a>
    <a style="left:985px">Contact us</a>
  </nav>
</header>

<section class="hero abs">
  <div class="hero-photo abs" role="img" aria-label="Black and white photo of a person with handcuffed hands behind the back"></div>
  <h1 class="hero-title abs">Delmara &amp; Castell<br>Advocates</h1>
  <a class="btn-ghost abs">Learn More</a>
  <div class="hero-dots abs"><span class="on"></span><span></span><span></span><span></span></div>
</section>

<section class="practice abs">
  <h2 class="section-title abs">Our Practice Areas</h2>
  <article class="area-card abs" style="left:144px">
    <div class="area-photo" role="img" aria-label="Dark photo of handcuffed hands"><h3>Criminal</h3></div>
    <p>Sed ut perspiciatis unde omnis iste natus error sit voluptatem accusantium doloremque laudantium, totam rem aperiam, eaque ipsa quae ab illo inventore veritatis et quasi architecto beatae vitae dicta sunt explicabo. Nemo enim ipsam voluptatem quia voluptas sit aspernatur</p>
    <a class="btn-read">Read More</a>
  </article>
  <article class="area-card abs" style="left:378px">
    <div class="area-photo" role="img" aria-label="Dark photo of a person opening a shirt to show a flag print"><h3>Citizenship &amp;<br>Residence</h3></div>
    <p>Sed ut perspiciatis unde omnis iste natus error sit voluptatem accusantium doloremque laudantium, totam rem aperiam, eaque ipsa quae ab illo inventore veritatis et quasi architecto beatae vitae dicta sunt explicabo. Nemo enim ipsam voluptatem quia voluptas sit aspernatur</p>
    <a class="btn-read">Read More</a>
  </article>
  <article class="area-card abs" style="left:611px">
    <div class="area-photo" role="img" aria-label="Dark photo of a silhouetted businessman by a window"><h3>Sovereign Patron<br>Pathway</h3></div>
    <p>Sed ut perspiciatis unde omnis iste natus error sit voluptatem accusantium doloremque laudantium, totam rem aperiam, eaque ipsa quae ab illo inventore veritatis et quasi architecto beatae vitae dicta sunt explicabo. Nemo enim ipsam voluptatem quia voluptas sit aspernatur</p>
    <a class="btn-read">Read More</a>
  </article>
  <article class="area-card abs" style="left:845px">
    <div class="area-photo" role="img" aria-label="Dark photo of a judge's gavel and bullets on a desk"><h3>Criminal<br>Defence</h3></div>
    <p>Sed ut perspiciatis unde omnis iste natus error sit voluptatem accusantium doloremque laudantium, totam rem aperiam, eaque ipsa quae ab illo inventore veritatis et quasi architecto beatae vitae dicta sunt explicabo. Nemo enim ipsam voluptatem quia voluptas sit aspernatur</p>
    <a class="btn-read">Read More</a>
  </article>
  <div class="scroll-track abs"><div class="scroll-thumb abs"></div></div>
</section>

<section class="news-band abs"><h2 class="section-title abs">Latest News</h2></section>
<svg class="news-pointer abs" width="28" height="15" viewBox="0 0 28 15"><path d="M0 0H28L14 15Z" fill="#050505"/></svg>

<section class="news abs">
  <svg class="nav-arrow abs" style="left:58px" width="16" height="26" viewBox="0 0 16 26"><path d="M13 2 3 13l10 11" fill="none" stroke="#777" stroke-width="3"/></svg>
  <svg class="nav-arrow abs" style="left:1125px" width="16" height="26" viewBox="0 0 16 26"><path d="M3 2l10 11L3 24" fill="none" stroke="#777" stroke-width="3"/></svg>
  <article class="news-card abs" style="left:144px">
    <div class="news-photo" role="img" aria-label="Close-up photo of printed dictionary text about advocates"><div class="news-date">June<br>8th<br>2016</div></div>
    <h4>Sed ut perspiciatis unde omnis iste natus error sit voluptatem accusantium doloremque...</h4>
    <p>Totam rem aperiam, eaque ipsa quae ab illo inventore veritatis et quasi architecto beatae vitae dicta sunt explicabo. Nemo enim ipsam voluptatem quia voluptas sit aspernatur</p>
    <a class="btn-read">Read More</a>
  </article>
  <article class="news-card abs" style="left:457px">
    <div class="news-photo" role="img" aria-label="Photo of lawyers meeting around a table"><div class="news-date">June<br>8th<br>2016</div></div>
    <h4>Sed ut perspiciatis unde omnis iste natus error sit voluptatem accusantium doloremque...</h4>
    <p>Totam rem aperiam, eaque ipsa quae ab illo inventore veritatis et quasi architecto beatae vitae dicta sunt explicabo. Nemo enim ipsam voluptatem quia voluptas sit aspernatur</p>
    <a class="btn-read">Read More</a>
  </article>
  <article class="news-card abs" style="left:768px">
    <div class="news-photo" role="img" aria-label="Photo of colleagues reviewing documents at a desk"><div class="news-date">June<br>8th<br>2016</div></div>
    <h4>Sed ut perspiciatis unde omnis iste natus error sit voluptatem accusantium doloremque...</h4>
    <p>Totam rem aperiam, eaque ipsa quae ab illo inventore veritatis et quasi architecto beatae vitae dicta sunt explicabo. Nemo enim ipsam voluptatem quia voluptas sit aspernatur</p>
    <a class="btn-read">Read More</a>
  </article>
</section>

<section class="testimonials abs" role="img" aria-label="Dark background photo of business people in an office">
  <h2 class="section-title abs">Client Testimonials</h2>
  <div class="partner abs"><i></i><span>Harbourline Alliance</span></div>
  <div class="quote-divider abs"></div>
  <p class="quote abs">Lorem Ipsum is simply dummy text of the printing and typesetting industry. Lorem Ipsum has been the industry's standard dummy text ever since the 1500s, when an unknown printer took a galley of type and scrambled it to make a type specimen book. It has survived not only five centuries</p>
  <div class="quote-nav abs">
    <svg width="12" height="20" viewBox="0 0 12 20"><path d="M10 2 2 10l8 8" fill="none" stroke="#fff" stroke-width="2.5"/></svg>
    <span class="sep"></span>
    <svg width="12" height="20" viewBox="0 0 12 20"><path d="M2 2l8 8-8 8" fill="none" stroke="#fff" stroke-width="2.5"/></svg>
  </div>
</section>

<footer class="site-footer abs">
  <div class="wordmark abs">Delmara &amp; Castell Advocates</div>
  <div class="footer-rule abs"></div>
  <ul class="footer-col abs" style="left:142px"><li>Home</li><li>About Us</li><li>Practice Areas</li><li>About Malta</li><li>Contact us</li></ul>
  <ul class="footer-col abs" style="left:300px"><li>Criminal</li><li>Citizenship &amp; Residence</li><li>Sovereign Patron Pathway</li><li>Criminal Defence</li><li>Civil Litigation</li></ul>
  <ul class="footer-col abs" style="left:534px"><li>Arbitration and ADR</li><li>Commercial and Corporate</li><li>Media Law.</li></ul>
  <ul class="footer-col abs" style="left:741px"><li>Castell Chambers</li><li>Triq il-Merkanti 42</li><li>VLT 1170 Valletta &nbsp;|&nbsp; Malta</li><li>Telephone: +356 2100 4821</li><li>E-mail: office@delmaracastell.example</li></ul>
  <ul class="footer-col social abs" style="left:977px"><li>Circlebook <b></b></li><li>Chirper <b></b></li><li>Linkwork <b></b></li></ul>
</footer>

<section class="legal abs">
  <p class="legal-text abs"><em>Terms &amp; Privacy :</em> Lorem ipsum dolor sit amet, consectetur adipiscing elit, sed do eiusmod tempor incididunt ut labore et dolore magna aliqua. Ut enim ad minim veniam, quis nostrud exercitation ullamco laboris Lorem ipsum dolor sit amet, consectetur adipiscing elit.</p>
  <div class="legal-rule abs"></div>
  <p class="copyright abs">© 2016 Company Name &nbsp;|&nbsp; All Rights Reserved</p>
</section>

</body>
</html>
```